Builder of high-end, expensive tables and other furniture

Build a website that represents what we do. I want a luxury feel that appeals to those who can afford our products. We build very high end tables and other furniture using trees that have fallen or are standing dead. We never cut living trees. Trees are harvested, milled, and kiln dried. Then that lumber is meticulously turned into fine furniture using the best equipment. Our furniture prices range from $1,000-$20,000.

Trying to figure out how to raise my spend.

```html
<!DOCTYPE html>
<html lang="en">
<head>
<meta charset="utf-8">
<title>Heartwood Atelier — Sustainable Luxury Furniture</title>
<link rel="stylesheet" href="https://fonts.googleapis.com/css2?family=Marcellus&family=DM+Sans:wght@400;500;700&display=swap">
<style>
:root{
  --orange:#e8612c;
  --orange-light:#f39358;
  --blue:#0a4fae;
  --blue-label:#2a66b8;
  --ink:#1d1d1d;
  --text:#3d3d3d;
  --muted:#6b6b6b;
  --panel:#efefef;
  --dark:#1c1c1c;
  --white:#ffffff;
  --card-line:#e88a66;
}
*{box-sizing:border-box;margin:0;padding:0}
html,body{width:1200px;height:3656px;overflow:hidden}
body{font-family:"DM Sans",sans-serif;color:var(--text);background:var(--white);position:relative}
.display{font-family:"Marcellus",serif;font-weight:400}
section,header,footer{position:absolute;left:0;width:1200px}
.abs{position:absolute}
.btn{position:absolute;display:flex;align-items:center;justify-content:center;border-radius:5px;font-family:"Marcellus",serif;font-size:19px;color:var(--white);background:linear-gradient(90deg,var(--orange),var(--orange-light));width:154px;height:46px}
.label{font-size:15px;letter-spacing:.3px;color:var(--blue-label);text-transform:uppercase}

/* Hero */
.hero{top:0;height:617px;background:linear-gradient(120deg,#1b1d22 0%,#2a2c30 45%,#3a3b3a 70%,#22252a 100%)}
.brand{position:absolute;display:flex;align-items:center;gap:10px;font-family:"Marcellus",serif;font-size:33px;color:var(--orange)}
.brand .mark{width:14px;height:14px;border-radius:50%;background:var(--orange)}
.nav{position:absolute;top:48px;left:554px;display:flex;gap:34px;font-size:15px;color:var(--white)}
.cart{position:absolute;left:1056px;top:48px}
.hero h1{position:absolute;left:120px;top:202px;font-size:48px;line-height:54px;color:var(--white);width:560px}
.hero p{position:absolute;left:122px;top:382px;font-size:15px;line-height:22px;color:#eaeaea;width:400px}

/* Pattern band */
.pattern{top:617px;height:1167px;background:linear-gradient(135deg,#ffffff 0%,#fdf3ee 40%,#ffffff 60%,#fcefe8 100%)}
.about-panel{position:absolute;left:122px;top:99px;width:956px;height:450px;background:var(--panel)}
.about-photo{position:absolute;left:0;top:136px;width:550px;height:376px;background:radial-gradient(ellipse at 50% 45%,#8a5a34 0%,#4a3424 40%,#1a1714 100%)}
.about-text{position:absolute;left:641px;top:156px;width:400px}
.about-text h2{font-size:30px;line-height:37px;color:var(--ink);margin-top:9px;letter-spacing:-.3px}
.about-text p{font-size:14px;line-height:22.5px;color:var(--text);margin-top:20px;width:350px}
.about-text p .name{color:var(--orange)}
.btn-outline{margin-top:24px;width:155px;height:46px;border:1.5px solid #444;border-radius:5px;display:flex;align-items:center;justify-content:center;font-family:"Marcellus",serif;font-size:19px;color:var(--ink)}

.shop-head{position:absolute;top:662px;width:1200px;text-align:center}
.shop-head h2{font-size:31px;color:var(--ink);margin-top:6px}
.cards{position:absolute;left:122px;top:749px;display:flex;gap:15px}
.card{width:180px;height:222px;border:1.5px solid var(--card-line);background:var(--white);text-align:center}
.card .photo{height:175px}
.card .title{font-size:14px;color:#5e8ac9;margin-top:4px}
.card .price{font-size:11px;color:var(--ink);margin-top:1px}
.circle-btn{position:absolute;width:36px;height:36px;border-radius:50%;background:var(--white);border:1px solid #9a9a9a;display:flex;align-items:center;justify-content:center}

/* Why us */
.why{top:1784px;height:581px}
.why-panel{position:absolute;left:0;top:0;width:642px;height:581px;background:var(--blue)}
.why-photo{position:absolute;left:642px;top:0;width:558px;height:581px;background:linear-gradient(160deg,#e9e6df 0%,#8c5a38 35%,#4a2a18 70%,#2a1a10 100%)}
.why .label{position:absolute;left:122px;top:62px;color:#6f93cf}
.why h2{position:absolute;left:120px;top:84px;font-size:31px;color:var(--white)}
.feature{position:absolute;left:119px;width:440px}
.feature .ft{display:flex;align-items:center;gap:12px;font-size:13px;font-weight:500;color:var(--white);text-transform:uppercase}
.feature .ft svg{flex:none}
.feature p{font-size:12.5px;line-height:20px;color:#d8e2f3;margin-top:8px}

/* Testimonials */
.testimonials{top:2365px;height:488px;background:linear-gradient(135deg,#ffffff 0%,#fcf1ea 50%,#ffffff 100%)}
.t-head{position:absolute;top:100px;width:1200px;text-align:center}
.t-head h2{font-size:31px;color:var(--ink);margin-top:4px}
.stars{position:absolute;top:182px;left:556px;display:flex;gap:6px}
.quote{position:absolute;top:218px;left:285px;width:630px;text-align:center;font-size:14.5px;line-height:24px;color:var(--text)}
.author{position:absolute;top:327px;left:514px;display:flex;align-items:center;gap:13px;font-size:14.5px;font-weight:500;color:var(--ink)}
.avatar{width:36px;height:36px;border-radius:50%;border:2px solid #4d79c0;background:#e4ddd5}
.dots{position:absolute;top:401px;left:571px;display:flex;gap:8px;align-items:center}
.dots span{width:5px;height:5px;border-radius:50%;background:var(--ink)}
.dots .active{width:14px;height:14px;border:1.5px solid var(--orange);background:radial-gradient(circle,var(--orange) 30%,transparent 32%)}

/* CTA */
.cta{top:2853px;height:399px;background:radial-gradient(ellipse at 35% 30%,#5a3f2a 0%,#2e2218 45%,#17120e 100%)}
.cta h2{position:absolute;top:106px;width:1200px;text-align:center;font-size:47px;line-height:54px;color:var(--white)}
.cta p{position:absolute;top:223px;left:410px;width:380px;text-align:center;font-size:13px;line-height:20px;color:#e8e8e8}

/* Footer */
.footer{top:3252px;height:404px;background:var(--dark);color:var(--white)}
.footer h3{position:absolute;font-family:"DM Sans",sans-serif;font-weight:500;font-size:17px;text-transform:uppercase}
.footer h3::after{content:"";position:absolute;left:86px;top:30px;width:20px;height:2px;background:var(--blue)}
.footer ul{position:absolute;list-style:none;font-size:15px;color:#d9d9d9}
.footer li{height:29.5px}
.contact-item{position:absolute;display:flex;gap:14px;font-size:15px;line-height:23px;color:#d9d9d9}
.socials{position:absolute;left:148px;top:163px;display:flex;gap:16px}
.socials span{width:17px;height:17px;border:1.8px solid var(--orange);border-radius:50%}
.divider{position:absolute;left:120px;top:297px;width:960px;height:1px;background:#3a3a3a}
.copyright{position:absolute;top:337px;width:1200px;text-align:center;font-size:13px;color:#cfcfcf}
</style>
</head>
<body>

<header class="hero">
  <div class="brand" style="left:120px;top:30px"><span class="mark"></span>Heartwood Atelier</div>
  <nav class="nav"><span>Home</span><span>About Us</span><span>Products</span><span>Testimonials</span><span>Contact</span></nav>
  <svg class="cart" width="18" height="20" viewBox="0 0 18 20" aria-label="Cart"><path d="M3 6h12l-1 13H4z" fill="none" stroke="#fff" stroke-width="2"/><path d="M6 6V4a3 3 0 0 1 6 0v2" fill="none" stroke="#fff" stroke-width="2"/><circle cx="15" cy="3" r="3" fill="#e8612c"/></svg>
  <h1 class="display">Discover Timeless Elegance in Sustainable Luxury Furniture</h1>
  <p>Experience the Artistry of Nature Transformed into Unparalleled Furniture Creations</p>
  <div class="btn" style="left:122px;top:453px">Shop Now</div>
</header>

<section class="pattern">
  <div class="about-panel"></div>
  <div class="about-photo" role="img" aria-label="Walnut table with a spiral inlay top on black angular legs"></div>
  <div class="about-text">
    <div class="label">About Us</div>
    <h2 class="display">Redefining Luxury with<br>Sustainable Craftsmanship</h2>
    <p>At <span class="name">Heartwood Atelier</span>, we redefine the concept of luxury furniture with our unwavering commitment to sustainability and uncompromising craftsmanship. Our exquisite tables and furniture embody timeless elegance and offer a touch of opulence to the discerning clientele who appreciate the finer things in life.</p>
    <div class="btn-outline">Read More</div>
  </div>

  <div class="shop-head">
    <div class="label">Shop</div>
    <h2 class="display">Featured Products</h2>
  </div>
  <div class="cards">
    <div class="card"><div class="photo" role="img" aria-label="Sculpted wooden lounge chair" style="background:linear-gradient(160deg,#6b4a33,#3a2a20 60%,#d8d2cb)"></div><div class="title">Lorem ipsum dolor</div><div class="price">$1000.00 - $1599.00</div></div>
    <div class="card"><div class="photo" role="img" aria-label="Live-edge side table on black legs" style="background:linear-gradient(180deg,#121212,#3a2a1c 50%,#0e0e0e)"></div><div class="title">Lorem ipsum dolor</div><div class="price">$1000.00 - $1599.00</div></div>
    <div class="card"><div class="photo" role="img" aria-label="Slatted wood armchair with cushions" style="background:linear-gradient(180deg,#7a7a78,#b9b2a6 55%,#585552)"></div><div class="title">Lorem ipsum dolor</div><div class="price">$1000.00 - $1599.00</div></div>
    <div class="card"><div class="photo" role="img" aria-label="Round slab coffee table with black base" style="background:linear-gradient(180deg,#e9e4de,#d7b8a2 55%,#2a2a2a)"></div><div class="title">Lorem ipsum dolor</div><div class="price">$1000.00 - $1599.00</div></div>
    <div class="card"><div class="photo" role="img" aria-label="Brown leather channel-tufted chair" style="background:linear-gradient(160deg,#2c2624,#7a4a30 50%,#1e1a18)"></div><div class="title">Lorem ipsum dolor</div><div class="price">$1000.00 - $1599.00</div></div>
  </div>
  <div class="circle-btn" style="left:103px;top:843px"><svg width="8" height="12" viewBox="0 0 8 12"><path d="M6 1 1 6l5 5" fill="none" stroke="#333" stroke-width="1.5"/></svg></div>
  <div class="circle-btn" style="left:1059px;top:843px"><svg width="8" height="12" viewBox="0 0 8 12"><path d="M2 1l5 5-5 5" fill="none" stroke="#333" stroke-width="1.5"/></svg></div>
  <div class="btn" style="left:523px;top:1011px">Shop Now</div>
</section>

<section class="why">
  <div class="why-panel"></div>
  <div class="why-photo" role="img" aria-label="Wooden bar stool beside a wicker basket in a warm kitchen"></div>
  <div class="label">Why Us</div>
  <h2 class="display">Sustainable Luxury Redefined</h2>
  <div class="feature" style="top:152px">
    <div class="ft"><svg width="30" height="26" viewBox="0 0 30 26"><path d="M2 20h10l8-4" fill="none" stroke="#fff" stroke-width="2"/><circle cx="19" cy="8" r="6" fill="none" stroke="#e8612c" stroke-width="2"/></svg>Sustainable Excellence</div>
    <p>We prioritize nature by using dead trees for furniture, promoting ecological harmony and sustainability while providing luxurious options.</p>
  </div>
  <div class="feature" style="top:245px">
    <div class="ft"><svg width="30" height="30" viewBox="0 0 30 30"><circle cx="15" cy="13" r="9" fill="none" stroke="#fff" stroke-width="2"/><circle cx="15" cy="13" r="4" fill="#e8612c"/></svg>Impeccable Craftsmanship</div>
    <p>Our experienced and passionate artisans use the finest techniques and tools to meticulously craft furniture with unparalleled quality.</p>
  </div>
  <div class="feature" style="top:339px">
    <div class="ft"><svg width="30" height="30" viewBox="0 0 30 30"><rect x="3" y="9" width="16" height="16" fill="none" stroke="#fff" stroke-width="2"/><rect x="11" y="3" width="16" height="16" fill="none" stroke="#e8612c" stroke-width="2"/></svg>Exceptional Materials</div>
    <p>We choose superior lumber that's harvested, milled, and kiln-dried, enhancing its natural beauty to produce charming furniture.</p>
  </div>
  <div class="feature" style="top:434px">
    <div class="ft"><svg width="30" height="28" viewBox="0 0 30 28"><rect x="3" y="4" width="24" height="10" rx="3" fill="#e8612c"/><path d="M3 14h24M7 14v10M23 14v10" stroke="#fff" stroke-width="2"/></svg>Unparalleled Design</div>
    <p>Our furniture designs blend classic elegance and modern aesthetics, with styles ranging from minimalistic to ornate detailing to suit diverse tastes and interiors.</p>
  </div>
</section>

<section class="testimonials">
  <div class="t-head">
    <div class="label">Testimonials</div>
    <h2 class="display">What Our Client Say</h2>
  </div>
  <div class="stars">
    <svg width="84" height="14" viewBox="0 0 84 14" aria-label="Five stars"><g fill="#e8612c"><path id="s" d="M7 0l2 5h5l-4 3 2 5-5-3-5 3 2-5-4-3h5z"/><use href="#s" x="17.5"/><use href="#s" x="35"/><use href="#s" x="52.5"/><use href="#s" x="70"/></g></svg>
  </div>
  <p class="quote">Lorem ipsum dolor sit amet consectetur. Morbi et turpis eget ac cras sit curabitur. Ut consequat proin eget nam nunc massa pharetra pharetra gravida. Nunc adipiscing sit in ut at duis turpis felis velit. Nulla dui posuere eget orci tellus metus scelerisque aliquet gravida. Id porttitor donec et est.</p>
  <div class="author"><span class="avatar" role="img" aria-label="Client portrait"></span>Maren Castell</div>
  <div class="dots"><span class="active"></span><span></span><span></span><span></span></div>
  <div class="circle-btn" style="left:135px;top:230px;border-color:#333"><svg width="8" height="12" viewBox="0 0 8 12"><path d="M6 1 1 6l5 5" fill="none" stroke="#333" stroke-width="2"/></svg></div>
  <div class="circle-btn" style="left:1017px;top:230px;border-color:#333"><svg width="8" height="12" viewBox="0 0 8 12"><path d="M2 1l5 5-5 5" fill="none" stroke="#333" stroke-width="2"/></svg></div>
</section>

<section class="cta" role="img" aria-label="Dim workshop table with lamp glow behind the banner text">
  <h2 class="display">Immerse Yourself In<br>Sustainable Luxury</h2>
  <p>Explore our Captivating Collection and Elevate Your Living Spaces Today!</p>
  <div class="btn" style="left:523px;top:278px">Shop Now</div>
</section>

<footer class="footer">
  <div class="brand" style="left:125px;top:80px"><span class="mark"></span>Heartwood Atelier</div>
  <div class="abs" style="left:148px;top:130px;font-size:17px">FOLLOW US</div>
  <div class="socials" aria-label="Social links"><span></span><span></span><span></span></div>
  <h3 style="left:554px;top:56px">Quick Links</h3>
  <ul style="left:557px;top:110px"><li>Home</li><li>About Us</li><li>Products</li><li>Testimonials</li><li>Contact</li></ul>
  <h3 style="left:771px;top:57px">Contact</h3>
  <div class="contact-item" style="left:771px;top:115px"><svg width="14" height="18" viewBox="0 0 14 18"><path d="M7 17s6-6 6-10A6 6 0 0 0 1 7c0 4 6 10 6 10z" fill="#e8612c"/><circle cx="7" cy="7" r="2.2" fill="#1c1c1c"/></svg><span>418 Alder Grove Ln. Fernvale,<br>Oregon 97210</span></div>
  <div class="contact-item" style="left:771px;top:170px"><svg width="14" height="14" viewBox="0 0 14 14"><path d="M3 1l3 3-2 2c1 2 2 3 4 4l2-2 3 3-2 2C6 13 1 8 1 3z" fill="#e8612c"/></svg><span>(503) 555-0187</span></div>
  <div class="contact-item" style="left:771px;top:202px"><svg width="15" height="12" viewBox="0 0 15 12"><rect x="0" y="1" width="15" height="10" fill="#e8612c"/><path d="M0 1l7.5 6L15 1" fill="none" stroke="#1c1c1c" stroke-width="1.4"/></svg><span>hello@heartwoodatelier.example</span></div>
  <div class="divider"></div>
  <div class="copyright">Copyright Heartwood Atelier | All rights reserved</div>
</footer>

</body>
</html>
```